QVR business card

Need a business card for a company that provides instructional design and elearning development services. The website is here: http://quorvane.studio/

I'm attaching a current logo, as well as the old business card design. While I like to keep it clean, the old design is too simplistic for my liking. The only idea I want to reuse from the old design is placing industry jargon on the back of the card, just need a better way to present it. But if you have other ideas for the back--feel free to experiment.

Please use the colors complementary to the color we have on the website. Thank you!

```html
<!DOCTYPE html>
<html lang="en">
<head>
<meta charset="utf-8">
<title>QVR business card</title>
<link rel="stylesheet" href="https://fonts.googleapis.com/css2?family=Roboto:wght@400;500;700;900&display=swap">
<style>
  :root {
    --teal: #1fa98f;
    --teal-dark: #148572;
    --ink: #1e1e1e;
    --paper: #f3f3f3;
    --paper-shade: #d6d8d9;
    --stage: #2a2a2a;
    --night: #0d0d0d;
    --white: #ffffff;
  }
  * { margin: 0; padding: 0; box-sizing: border-box; }
  html, body {
    width: 1200px;
    height: 997px;
    overflow: hidden;
    background: var(--stage);
    font-family: "Roboto", Arial, sans-serif;
  }
  .sheet {
    position: relative;
    width: 1200px;
    height: 997px;
    display: flex;
    align-items: center;
    justify-content: center;
    gap: 40px;
  }
  .card {
    width: 540px;
    height: 310px;
    border-radius: 14px;
    overflow: hidden;
    box-shadow: 0 18px 40px rgba(0,0,0,.55);
  }
  .card svg { display: block; width: 540px; height: 310px; }
  .brand { font-family: "Roboto", Arial, sans-serif; font-weight: 900; fill: var(--teal); }
  .person-name { font-weight: 900; fill: var(--ink); letter-spacing: 1px; }
  .person-role { font-weight: 700; fill: var(--teal); letter-spacing: 2px; }
  .contact { font-weight: 500; fill: var(--white); }
  .service-label { font-weight: 900; fill: var(--ink); font-size: 11px; letter-spacing: .5px; }
  .visit { font-weight: 500; fill: var(--teal); }
  .web { font-weight: 700; fill: var(--white); }
</style>
</head>
<body>
<main class="sheet">

  <!-- Front of card -->
  <section class="card card--front">
    <svg viewBox="0 0 540 310" xmlns="http://www.w3.org/2000/svg">
      <defs>
        <linearGradient id="frontPaper" x1="0" y1="0" x2="0" y2="1">
          <stop offset="0" stop-color="#fafafa"/>
          <stop offset="1" stop-color="#dfe1e2"/>
        </linearGradient>
        <linearGradient id="frontPhoto" x1="0" y1="0" x2="1" y2="1">
          <stop offset="0" stop-color="#e4e6e7"/>
          <stop offset=".5" stop-color="#c3c7ca"/>
          <stop offset="1" stop-color="#d9dcde"/>
        </linearGradient>
      </defs>
      <rect class="card-base" width="540" height="310" fill="url(#frontPaper)"/>
      <rect class="photo-collage" x="0" y="42" width="540" height="214" fill="url(#frontPhoto)" opacity=".7"
            role="img" aria-label="Hexagon collage of business and e-learning photographs"/>
      <rect class="rule" x="0" y="28" width="540" height="2" fill="var(--teal)"/>
      <rect class="rule" x="0" y="250" width="540" height="2" fill="var(--teal)"/>

      <g class="logo">
        <circle cx="238" cy="90" r="9" fill="var(--ink)"/>
        <text class="brand" x="254" y="101" font-size="34">QVR</text>
      </g>

      <text class="person-name" x="270" y="160" font-size="26" text-anchor="middle">MAREK HALVORSEN</text>
      <text class="person-role" x="270" y="182" font-size="14" text-anchor="middle">OWNER</text>

      <rect class="contact-band" x="0" y="258" width="540" height="52" fill="var(--teal)"/>
      <g class="contact-row">
        <circle cx="26" cy="284" r="10" fill="var(--white)"/>
        <path d="M21 279 q1 -2 3 -1 l1 3 -2 1 q1 3 4 4 l1 -2 3 1 q1 2 -1 3 q-8 0 -9 -9z" fill="var(--teal)"/>
        <text class="contact" x="42" y="289" font-size="13">555-010-4821</text>

        <circle cx="178" cy="284" r="10" fill="var(--white)"/>
        <rect x="172" y="280" width="12" height="8" fill="none" stroke="var(--teal)" stroke-width="1.5"/>
        <path d="M172 280 l6 5 6 -5" fill="none" stroke="var(--teal)" stroke-width="1.5"/>
        <text class="contact" x="194" y="289" font-size="13">mhalvorsen@quorvane.studio</text>

        <circle cx="384" cy="284" r="10" fill="var(--white)"/>
        <circle cx="384" cy="284" r="6" fill="none" stroke="var(--teal)" stroke-width="1.5"/>
        <path d="M378 284 h12 M384 278 v12" stroke="var(--teal)" stroke-width="1.2"/>
        <text class="contact" x="400" y="289" font-size="13">www.quorvane.studio</text>
      </g>
    </svg>
  </section>

  <!-- Back of card -->
  <section class="card card--back">
    <svg viewBox="0 0 540 310" xmlns="http://www.w3.org/2000/svg">
      <defs>
        <linearGradient id="backPhoto" x1="0" y1="0" x2="1" y2="1">
          <stop offset="0" stop-color="#eef0f1"/>
          <stop offset=".55" stop-color="#c9cdd0"/>
          <stop offset="1" stop-color="#8f9499"/>
        </linearGradient>
      </defs>
      <rect class="photo-collage" width="540" height="310" fill="url(#backPhoto)"
            role="img" aria-label="Hexagon collage of business photographs with a man in a suit and tie"/>

      <g class="logo">
        <circle cx="32" cy="56" r="9" fill="var(--ink)"/>
        <text class="brand" x="48" y="67" font-size="34">QVR</text>
      </g>

      <path class="wave-band" d="M0 250 C170 248 320 185 420 150 S510 118 540 116 L540 310 L0 310 Z" fill="var(--teal)"/>
      <path class="wave-light" d="M0 262 C170 260 320 198 420 163 S510 132 540 130 L540 310 L0 310 Z" fill="#5cc7b3"/>
      <path class="wave-night" d="M0 276 C170 274 320 212 420 177 S510 148 540 146 L540 310 L0 310 Z" fill="var(--night)"/>

      <g class="service">
        <text class="service-label" x="70" y="212" text-anchor="middle">INSTRUCTIONAL</text>
        <text class="service-label" x="70" y="226" text-anchor="middle">DESIGN</text>
        <circle cx="70" cy="262" r="26" fill="var(--teal)" stroke="#dcdcdc" stroke-width="3"/>
        <path d="M60 256 h6 a4 4 0 1 1 8 0 h6 v6 a4 4 0 1 1 0 8 v4 h-20z" fill="var(--white)"/>
      </g>

      <g class="service">
        <text class="service-label" x="198" y="184" text-anchor="middle">E-LEARNING</text>
        <text class="service-label" x="198" y="198" text-anchor="middle">DEVELOPMENT</text>
        <circle cx="198" cy="236" r="26" fill="var(--teal)" stroke="#dcdcdc" stroke-width="3"/>
        <path d="M187 228 h17 v8 a6 6 0 0 1 -6 6 h-5 a6 6 0 0 1 -6 -6z" fill="var(--white)"/>
        <path d="M204 230 a4 4 0 0 1 0 8" fill="none" stroke="var(--white)" stroke-width="2"/>
        <rect x="185" y="244" width="22" height="2" fill="var(--white)"/>
      </g>

      <g class="service">
        <text class="service-label" x="318" y="138" text-anchor="middle">MOBILE</text>
        <text class="service-label" x="318" y="152" text-anchor="middle">LEARNING</text>
        <circle cx="318" cy="192" r="26" fill="var(--teal)" stroke="#dcdcdc" stroke-width="3"/>
        <path d="M306 200 a6 6 0 0 1 1 -12 a8 8 0 0 1 15 -2 a6 6 0 0 1 2 14z" fill="var(--white)"/>
        <path d="M315 197 v-6 h-3 l6 -6 6 6 h-3 v6z" fill="var(--teal)"/>
      </g>

      <g class="service">
        <text class="service-label" x="436" y="98" text-anchor="middle">INSTRUCTOR-LED</text>
        <text class="service-label" x="436" y="112" text-anchor="middle">TRAINING</text>
        <circle cx="436" cy="150" r="26" fill="var(--teal)" stroke="#dcdcdc" stroke-width="3"/>
        <rect x="424" y="143" width="24" height="16" rx="2" fill="var(--white)"/>
        <rect x="431" y="140" width="10" height="4" fill="var(--white)"/>
        <circle cx="436" cy="151" r="5" fill="var(--teal)"/>
      </g>

      <text class="visit" x="520" y="238" font-size="16" text-anchor="end" letter-spacing="1">Visit us on</text>
      <text class="web" x="520" y="262" font-size="16" text-anchor="end" letter-spacing=".5">www.quorvane.studio</text>
    </svg>
  </section>

</main>
</body>
</html>
```